creation of a business card design for a company specializing in the creation...

I would like to create a design for a professional business card on a black background and with the company's colors (I am attaching some files: including the logo in horizontal and centered format, I am also attaching a recent project design a T-shirt, this is the one I chose to give you an idea of my preferences.

we are in the process of developing a new website design, it is still in the development phase but it can be viewed at the following address: www.vantrelmo.be to give you other ideas about the company
you will see for yourself the subject of my main activity: company specializing in the construction of stairs

I would like a business card that stands out from the rest with a unique design

here is the informations
Name: Lucien Barthel
Function: Manager
Address: Rue Moulinet du Parc 42
7180 Val-Moreuil
telephone: +32 468 219 804
email: info@rx7p.be
website: rx7p. be
social networks: Facebook, YouTube, TikTok, Instagram

Target Market(s)

customer who wants to have a beautiful staircase built

Industry/Entity Type

contruction d'escalier

Contact Information for Business Card

Adresse. Numero de telephone, site web, le texte : "Createur d'escalier", logo recto-verso, icone des reseaux sociaux

Requirements
Must have
• the mention: Stair creator
Nice to have
• an illustration of a designer staircase
Should not have
• do not distort the logo

```html
<!DOCTYPE html>
<html lang="fr">
<head>
<meta charset="utf-8">
<title>RX7P – Business Card</title>
<link rel="stylesheet" href="https://fonts.googleapis.com/css2?family=Oswald:wght@600&family=Poppins:wght@300;400;500&display=swap">
<style>
  :root {
    --page: #d9d9d9;
    --card-black: #050607;
    --card-slate: #1f252b;
    --facet: #2a3238;
    --steel-blue: #6f9ec4;
    --deep-blue: #2f5f80;
    --white: #f4f6f8;
    --muted: #9db6c9;
  }
  * { box-sizing: border-box; margin: 0; padding: 0; }
  html, body { width: 1200px; height: 900px; overflow: hidden; }
  body {
    background: var(--page);
    font-family: "Poppins", sans-serif;
    color: var(--white);
    position: relative;
  }
  .card {
    position: absolute;
    left: 250px;
    width: 700px;
    height: 400px;
    border-radius: 34px;
    overflow: hidden;
    background: linear-gradient(200deg, var(--card-slate) 0%, #0d1013 45%, var(--card-black) 100%);
    box-shadow: 0 10px 24px rgba(0,0,0,.25);
  }
  .card--front { top: 40px; }
  .card--back { top: 460px; }
  .facets { position: absolute; inset: 0; width: 100%; height: 100%; }

  /* Front */
  .badge {
    position: absolute;
    left: 50%; top: 50%;
    transform: translate(-50%, -50%);
    width: 330px;
    text-align: center;
  }
  .badge__tagline-top {
    font-family: "Oswald", sans-serif;
    font-weight: 600;
    font-size: 22px;
    letter-spacing: 2px;
    text-transform: uppercase;
    color: var(--white);
  }
  .badge__art {
    display: block;
    width: 200px; height: 170px;
    margin: 10px auto 8px;
    border-radius: 50%;
    background: radial-gradient(circle at 50% 45%, #3f7596 0%, var(--deep-blue) 45%, #10212d 100%);
    border: 6px solid var(--deep-blue);
  }
  .brand-name {
    font-family: "Poppins", sans-serif;
    font-weight: 300;
    color: var(--white);
    letter-spacing: 8px;
    line-height: 1;
  }
  .badge .brand-name { font-size: 52px; }
  .brand-sub {
    font-family: "Poppins", sans-serif;
    font-weight: 400;
    font-size: 12px;
    letter-spacing: 7px;
    text-transform: uppercase;
    color: var(--steel-blue);
    margin-top: 6px;
  }

  /* Back */
  .back-brand {
    position: absolute;
    left: 70px; top: 70px;
    display: flex; align-items: center; gap: 22px;
  }
  .back-brand__mark {
    width: 64px; height: 64px;
    background: var(--steel-blue);
  }
  .back-brand .brand-name { font-size: 64px; }
  .person { position: absolute; left: 70px; top: 215px; }
  .person__name {
    font-family: "Oswald", sans-serif;
    font-weight: 600;
    font-size: 34px;
    text-transform: uppercase;
    color: var(--steel-blue);
    line-height: 1.05;
  }
  .person__role { font-size: 18px; margin-bottom: 12px; }
  .contact-list { list-style: none; }
  .contact-list li {
    display: flex; align-items: center; gap: 12px;
    font-size: 19px; line-height: 1.35;
  }
  .contact-list svg { width: 18px; height: 18px; flex: none; }
  .aside { position: absolute; right: 60px; top: 150px; text-align: right; }
  .socials { display: flex; gap: 10px; justify-content: flex-end; margin-bottom: 14px; }
  .socials span {
    width: 34px; height: 34px; border-radius: 50%;
    border: 1.5px solid var(--muted);
  }
  .address { font-size: 18px; line-height: 1.35; }
</style>
</head>
<body>

<section class="card card--front" aria-label="Recto">
  <svg class="facets" viewBox="0 0 700 400" preserveAspectRatio="none" aria-hidden="true">
    <polygon points="430,0 700,0 700,220 560,130" fill="var(--facet)" opacity=".55"/>
    <polygon points="560,130 700,220 700,320" fill="#161b1f" opacity=".8"/>
  </svg>
  <div class="badge">
    <div class="badge__tagline-top">Créateur d'escalier</div>
    <div class="badge__art" role="img" aria-label="Illustration d'un escalier design dans un médaillon bleu"></div>
    <div class="brand-name">RX7P</div>
    <div class="brand-sub">Original staircases</div>
  </div>
</section>

<section class="card card--back" aria-label="Verso">
  <svg class="facets" viewBox="0 0 700 400" preserveAspectRatio="none" aria-hidden="true">
    <polygon points="300,0 700,0 700,240 520,300 240,340" fill="var(--facet)" opacity=".45"/>
    <polygon points="460,60 700,40 700,160 520,140" fill="#12171b" opacity=".6"/>
  </svg>

  <div class="back-brand">
    <span class="back-brand__mark" aria-hidden="true"></span>
    <div>
      <div class="brand-name">RX7P</div>
      <div class="brand-sub">Original staircases</div>
    </div>
  </div>

  <div class="person">
    <div class="person__name">Lucien Barthel</div>
    <div class="person__role">Manager</div>
    <ul class="contact-list">
      <li>
        <svg viewBox="0 0 24 24" aria-hidden="true"><path d="M6.6 10.8a15 15 0 0 0 6.6 6.6l2.2-2.2c.3-.3.7-.4 1-.2 1.1.4 2.3.6 3.6.6.6 0 1 .4 1 1V20c0 .6-.4 1-1 1A17 17 0 0 1 3 4c0-.6.4-1 1-1h3.5c.6 0 1 .4 1 1 0 1.3.2 2.5.6 3.6.1.3 0 .7-.2 1z" fill="var(--steel-blue)"/></svg>
        +32 468 219 804
      </li>
      <li>
        <svg viewBox="0 0 24 24" aria-hidden="true"><rect x="2" y="5" width="20" height="14" rx="1" fill="var(--steel-blue)"/><path d="M2 6l10 7 10-7" stroke="var(--card-black)" stroke-width="1.6" fill="none"/></svg>
        info@rx7p.be
      </li>
      <li>
        <svg viewBox="0 0 24 24" aria-hidden="true" fill="none" stroke="var(--steel-blue)" stroke-width="2"><circle cx="12" cy="12" r="9"/><ellipse cx="12" cy="12" rx="4" ry="9"/><path d="M3 12h18M5 7h14M5 17h14"/></svg>
        rx7p. be
      </li>
    </ul>
  </div>

  <div class="aside">
    <div class="socials" role="img" aria-label="Quatre icônes de réseaux sociaux">
      <span></span><span></span><span></span><span></span>
    </div>
    <p class="address">Rue Moulinet du Parc 42<br>7180 Val-Moreuil</p>
  </div>
</section>

</body>
</html>
```